BorrowNest Website design, we are a home loan / lending company

We are a finance broking company that can do mortgages / home loans, Car Loans, Commercial Loans, SMSF Loans, Business Loans, Personal Loans
We are looking for a simple website, not too busy, easy to navigate, something that prompts customers to action or call us.
I like the simplicity of the following websites:
https://www.velkarafinance.com.au/ - I like this website front page. I was thinking I have my logo, the one with the black background appear , then the toolbar at the top perhaps?
https://trevix.com.au/business-loans# - on this page there are images under finance that works for you that I like that concept.
https://dunmerel.com.au/contact/ - I like the Make an Appointment page
https://trevix.com.au/about-us - Simple but effective page design

Target Market(s)

Home Loan Customer

Industry/Entity Type

Finance / Home Loans

Coding

Coded - Design and coding required

Number of Pages Required

5+ page

Font styles to use
Serif

Colors
0094D4
00A9DD
6FCCEA
C7EBF8
E9F6FB

Requirements
Must have
• The following Heading s - Contact Us, About Us, Our People, Make an Appointment, Loan Options, Calculators, Reviews. I want to use the Logo colours I have in the zip files I uploaded.
Nice to have
• Simple clean design

```html
<!DOCTYPE html>
<html lang="en">
<head>
<meta charset="utf-8">
<title>BorrowNest – Home Loans &amp; Lending</title>
<link href="https://fonts.googleapis.com/css2?family=Poppins:wght@300;400;500;600;700&display=swap" rel="stylesheet">
<style>
:root{
  --blue:#0094D4;
  --cyan:#00A9DD;
  --bright:#00C8EE;
  --sky:#6FCCEA;
  --pale:#C7EBF8;
  --mist:#E9F6FB;
  --ink:#222;
  --text:#444;
  --navy:#0B1A2B;
  --white:#fff;
  --star:#F6B400;
}
*{margin:0;padding:0;box-sizing:border-box}
html,body{width:1200px;height:3709px;overflow:hidden}
body{font-family:"Poppins",sans-serif;color:var(--text);background:var(--white);position:relative}
a{color:inherit;text-decoration:none}
.abs{position:absolute}

/* hero */
.hero{position:absolute;left:0;top:0;width:1200px;height:686px;overflow:hidden;
  background:linear-gradient(100deg,#6d5a48 0%,#a08a72 30%,#cbbfae 55%,#8d7a66 80%,#5b4c40 100%)}
.hero-photo{position:absolute;inset:0}
.hero-shade{position:absolute;inset:0;background:linear-gradient(90deg,rgba(0,0,0,.35),rgba(0,0,0,0) 60%)}
.hero-ring{position:absolute;left:610px;top:168px;width:420px;height:420px;border-radius:50%;background:rgba(255,255,255,.9)}
.hero-people{position:absolute;left:650px;top:150px;width:480px;height:536px;border-radius:240px 240px 0 0;
  background:linear-gradient(180deg,#9a8673,#4f6e92 70%,#3d5878)}
.logo{position:absolute;left:110px;top:20px;font-size:37px;font-weight:600;color:var(--white);letter-spacing:-1px}
.topbar{position:absolute;top:34px;right:110px;display:flex;gap:34px;color:var(--white);font-size:16px;align-items:center}
.topbar span{display:flex;align-items:center;gap:10px}
.nav{position:absolute;top:106px;left:106px;display:flex;gap:34px;color:var(--white);font-size:16px;letter-spacing:.3px}
.hero-kicker{position:absolute;left:113px;top:290px;color:var(--white);font-size:40px;font-weight:500}
.hero-title{position:absolute;left:112px;top:340px;color:var(--white);font-size:62px;font-weight:600}
.btn{display:inline-block;background:linear-gradient(90deg,var(--bright),var(--blue));color:var(--white);font-weight:600;border-radius:30px}
.hero .btn{position:absolute;left:113px;top:436px;width:118px;height:42px;line-height:42px;text-align:center;font-size:15px}
.arrow{position:absolute;top:370px}

/* section heads */
.sec-head{position:absolute;left:0;width:1200px;text-align:center}
.sec-head svg{display:block;margin:0 auto 6px}
.sec-head h2{font-size:44px;font-weight:700;background:linear-gradient(90deg,var(--bright),var(--blue));-webkit-background-clip:text;background-clip:text;color:transparent}

/* services */
.blob{position:absolute;border-radius:50%;background:var(--pale)}
.card{position:absolute;width:307px;height:310px;background:var(--white);box-shadow:0 4px 18px rgba(0,0,0,.12);text-align:center;padding:30px 18px 0}
.card svg{display:block;margin:0 auto 12px}
.card h3{font-size:19px;font-weight:500;color:var(--ink);margin-bottom:16px}
.card p{font-size:15.5px;line-height:30px;color:var(--text)}
.card::after{content:"";position:absolute;left:103px;bottom:0;width:100px;height:7px;border-radius:10px 10px 0 0;background:var(--blue)}

/* about */
.about{position:absolute;left:0;top:1693px;width:1200px;height:384px;
  background:linear-gradient(120deg,var(--mist) 0%,var(--mist) 30%,#f3fafd 30%,#f3fafd 45%,var(--mist) 45%,var(--mist) 70%,#f3fafd 70%,#f3fafd 82%,var(--mist) 82%)}
.about p{position:absolute;left:195px;top:134px;width:810px;font-size:16px;line-height:30px;text-align:justify;text-align-last:center;color:var(--text)}

/* people */
.person{position:absolute;width:260px;text-align:center}
.avatar{width:162px;height:162px;border-radius:50%;margin:0 auto 20px;border:3px solid var(--bright);
  background:linear-gradient(180deg,#e8e8e8,#bfc6cc);border-bottom-width:10px}
.person h3{font-size:20px;font-weight:500;color:var(--ink);margin-bottom:12px}
.person p{font-size:16px;line-height:30px;text-align:justify;text-align-last:center}
.person a{display:inline-block;margin-top:12px;color:var(--blue);font-weight:500;font-size:15px;text-decoration:underline;text-underline-offset:4px}

/* reviews */
.reviews{position:absolute;left:0;top:2688px;width:1200px;height:496px;background:var(--mist)}
.review{position:absolute;top:174px;width:465px;height:246px;background:var(--white);box-shadow:0 3px 14px rgba(0,0,0,.08)}
.review .face{position:absolute;left:15px;top:25px;width:80px;height:80px;border-radius:50%;background:linear-gradient(160deg,var(--sky),#d9b7a2)}
.review .quote{position:absolute;left:18px;top:130px;font-size:110px;line-height:1;color:var(--pale);font-weight:700;font-family:Georgia,serif}
.review h4{position:absolute;left:113px;top:36px;font-size:19px;font-weight:500;color:var(--ink)}
.review .role{position:absolute;left:113px;top:63px;font-size:17px;color:var(--text)}
.review p{position:absolute;left:114px;top:100px;width:330px;font-size:15.5px;line-height:28px}
.stars{position:absolute;left:114px;top:200px;display:flex;gap:2px}

/* footer */
.footer{position:absolute;left:0;top:3184px;width:1200px;height:525px;background:var(--navy);color:var(--white)}
.news-label{position:absolute;left:190px;top:96px;font-size:22px;font-weight:600}
.news-form{position:absolute;left:455px;top:72px;width:468px;height:54px;background:var(--white);border-radius:30px;border:3px solid var(--white);display:flex;align-items:center}
.news-form span{flex:1;display:flex;align-items:center;gap:18px;padding-left:38px;color:#666;font-size:14px}
.news-form .btn{width:118px;height:46px;line-height:46px;text-align:center;font-size:16px}
.rule{position:absolute;left:111px;width:978px;height:1px;background:rgba(255,255,255,.2)}
.fcol{position:absolute;top:240px;font-size:14px}
.fcol h5{font-size:14px;font-weight:600;margin-bottom:18px;letter-spacing:.3px}
.fcol ul{list-style:none}
.fcol li{line-height:32px;display:flex;gap:12px;align-items:center}
.contact-row{display:flex;gap:20px;align-items:center;margin-bottom:22px}
.ring{width:28px;height:28px;border:1px solid var(--white);border-radius:50%;display:flex;align-items:center;justify-content:center;flex:none}
.socials{display:flex;gap:10px;margin-top:22px}
.socials i{width:32px;height:32px;border:1px solid var(--white);border-radius:50%;display:block}
.copy{position:absolute;top:488px;left:0;width:1200px;text-align:center;font-size:14px}
</style>
</head>
<body>

<header class="hero">
  <div class="hero-photo" role="img" aria-label="Photo of two smiling business owners in a workshop office"></div>
  <div class="hero-ring"></div>
  <div class="hero-people" role="img" aria-label="Two smiling colleagues seated together"></div>
  <div class="hero-shade"></div>
  <div class="logo">BorrowNest</div>
  <div class="topbar">
    <span><svg width="20" height="20" viewBox="0 0 24 24"><path fill="#00C8EE" d="M6.6 10.8a15 15 0 006.6 6.6l2.2-2.2c.3-.3.7-.4 1-.2 1.1.4 2.3.6 3.6.6.6 0 1 .4 1 1V20c0 .6-.4 1-1 1A17 17 0 013 4c0-.6.4-1 1-1h3.5c.6 0 1 .4 1 1 0 1.3.2 2.5.6 3.6.1.3 0 .7-.2 1z"/></svg>+1555-204-7391</span>
    <span><svg width="22" height="22" viewBox="0 0 24 24"><circle cx="12" cy="8" r="4.5" fill="#00C8EE"/><path d="M3 21c0-5 4-8 9-8s9 3 9 8z" fill="#00C8EE"/></svg>Log In</span>
  </div>
  <nav class="nav">
    <a>Home</a><a>Contact Us</a><a>About Us</a><a>Our People</a><a>Make an Appointment</a><a>Loan Options</a><a>Calculators</a><a>Reviews</a>
  </nav>
  <div class="hero-kicker">Welcome To</div>
  <h1 class="hero-title">Borrow Nest</h1>
  <a class="btn">Get Started</a>
  <svg class="arrow" style="left:36px" width="26" height="44" viewBox="0 0 26 44"><path d="M22 4L4 22l18 18" stroke="#fff" stroke-width="3" fill="none"/></svg>
  <svg class="arrow" style="left:1130px" width="26" height="44" viewBox="0 0 26 44"><path d="M4 4l18 18L4 40" stroke="#fff" stroke-width="3" fill="none"/></svg>
</header>

<!-- services -->
<div class="blob" style="left:989px;top:1174px;width:216px;height:216px"></div>
<div class="blob" style="left:40px;top:1459px;width:180px;height:180px"></div>
<div class="sec-head" style="top:756px">
  <svg width="22" height="22" viewBox="0 0 24 24"><path d="M12 3a9 9 0 018.5 6M21 12a9 9 0 01-15 6.7M3 12a9 9 0 013-6.7" stroke="#333" stroke-width="2.4" fill="none"/></svg>
  <h2>Our Services</h2>
</div>

<div class="card" style="left:111px;top:929px">
  <svg width="70" height="70" viewBox="0 0 70 70" fill="none" stroke="#0094D4" stroke-width="2.4"><path d="M12 34L35 12l23 22M18 28v22h34V28"/><circle cx="30" cy="32" r="3"/><circle cx="40" cy="42" r="3"/><path d="M41 30L29 44M6 58h16l10 4 22-8"/></svg>
  <h3>Mortgages / Home Loans</h3>
  <p>Sed ut perspiciatis unde omnis iste natus error sit volupt accusantium doloremq laudantium, totam rem aperiam, eaque ipsa quae ab.</p>
</div>
<div class="card" style="left:447px;top:908px">
  <svg width="70" height="70" viewBox="0 0 70 70" fill="none" stroke="#0094D4" stroke-width="2.4"><path d="M8 50h54v-10l-8-4-8-10H24l-8 10-8 4z"/><circle cx="20" cy="52" r="5"/><circle cx="50" cy="52" r="5"/><path d="M48 4l12 4v10c0 7-6 11-12 13-6-2-12-6-12-13V8z"/><path d="M43 17l4 4 7-7"/></svg>
  <h3>Car Loans</h3>
  <p>Sed ut perspiciatis unde omnis iste natus error sit volupt accusantium doloremq laudantium, totam rem aperiam, eaque ipsa quae ab.</p>
</div>
<div class="card" style="left:782px;top:929px">
  <svg width="70" height="70" viewBox="0 0 70 70" fill="none" stroke="#0094D4" stroke-width="2.4"><path d="M20 64V8h30v56M8 64h54M12 30h8v34M50 30h8v34"/><path d="M26 16h5v5h-5zM39 16h5v5h-5zM26 28h5v5h-5zM39 28h5v5h-5zM26 40h5v5h-5zM39 40h5v5h-5zM30 64v-10h10v10"/></svg>
  <h3>Commercial Loans</h3>
  <p>Sed ut perspiciatis unde omnis iste natus error sit volupt accusantium doloremq laudantium, totam rem aperiam, eaque ipsa quae ab.</p>
</div>
<div class="card" style="left:111px;top:1269px">
  <svg width="70" height="70" viewBox="0 0 70 70" fill="none" stroke="#0094D4" stroke-width="2.4"><path d="M28 8h16l-4 8c8 4 14 12 14 20 0 8-8 12-18 12S18 44 18 36c0-8 6-16 14-20z"/><path d="M4 48h12l14 6h10l22-10-6 12-20 8H16l-12-4z"/><path d="M40 26c-2-2-8-2-8 2s8 2 8 6-6 4-8 2M36 22v22"/></svg>
  <h3>SMSF Loans</h3>
  <p>Sed ut perspiciatis unde omnis iste natus error sit volupt accusantium doloremq laudantium, totam rem aperiam, eaque ipsa quae ab.</p>
</div>
<div class="card" style="left:447px;top:1269px">
  <svg width="70" height="70" viewBox="0 0 70 70" fill="none" stroke="#0094D4" stroke-width="2.4"><path d="M8 64h56M14 64V46h8v18M28 64V38h8v18M42 64V30h8v34M56 64V20h6v44M10 40l16-14 10 6 22-20M50 12h8v8"/></svg>
  <h3>Business Loans</h3>
  <p>Sed ut perspiciatis unde omnis iste natus error sit volupt accusantium doloremq laudantium, totam rem aperiam, eaque ipsa quae ab.</p>
</div>
<div class="card" style="left:782px;top:1269px">
  <svg width="70" height="70" viewBox="0 0 70 70" fill="none" stroke="#0094D4" stroke-width="2.4"><circle cx="35" cy="22" r="12"/><path d="M12 62c0-14 10-22 23-22s23 8 23 22z"/></svg>
  <h3>Personal Loans</h3>
  <p>Sed ut perspiciatis unde omnis iste natus error sit volupt accusantium doloremq laudantium, totam rem aperiam, eaque ipsa quae ab.</p>
</div>

<!-- about -->
<section class="about">
  <div class="sec-head" style="top:44px">
    <svg width="22" height="22" viewBox="0 0 24 24"><path d="M12 3a9 9 0 018.5 6M21 12a9 9 0 01-15 6.7M3 12a9 9 0 013-6.7" stroke="#333" stroke-width="2.4" fill="none"/></svg>
    <h2>About Us</h2>
  </div>
  <p>Sed ut perspiciatis unde omnis iste natus error sit voluptatem accusantium doloremque laudantium, totam rem aperiam, eaque ipsa quae ab illo inventore veritatis et quasi architecto beatae vitae dicta sunt explicabo. Nemo enim ipsam voluptatem quia voluptas sit aspernatur aut odit aut fugit, sed quia consequuntur magni dolores eos qui ratione voluptatem sequi nesciunt. Neque porro quisquam est, qui dolorem ipsum quia dolor sit amet, consectetur, adipisci velit, sed quia non numquam eius modi tempora incidunt ut labore et dolore magnam aliquam quaerat voluptatem.</p>
</section>

<!-- people -->
<div class="abs" style="left:1088px;top:2100px;width:260px;height:380px;border-radius:50%;border:2px solid var(--pale)"></div>
<div class="abs" style="left:1132px;top:2130px;width:240px;height:320px;border-radius:50%;background:var(--pale)"></div>
<div class="sec-head" style="top:2122px">
  <svg width="22" height="22" viewBox="0 0 24 24"><path d="M12 3a9 9 0 018.5 6M21 12a9 9 0 01-15 6.7M3 12a9 9 0 013-6.7" stroke="#333" stroke-width="2.4" fill="none"/></svg>
  <h2>Our People</h2>
</div>
<div class="person" style="left:127px;top:2255px">
  <div class="avatar" role="img" aria-label="Portrait of team member"></div>
  <h3>Daniel Hart</h3>
  <p>Neque porro quisquai dolorem ipsum quia dolor sit amet eque porro quisquam est, qui dolorem</p>
  <a>READ MORE</a>
</div>
<div class="person" style="left:470px;top:2255px">
  <div class="avatar" role="img" aria-label="Portrait of team member"></div>
  <h3>Daniel Hart</h3>
  <p>Neque porro quisquai dolorem ipsum quia dolor sit amet eque porro quisquam est, qui dolorem</p>
  <a>READ MORE</a>
</div>
<div class="person" style="left:813px;top:2255px">
  <div class="avatar" role="img" aria-label="Portrait of team member"></div>
  <h3>Daniel Hart</h3>
  <p>Neque porro quisquai dolorem ipsum quia dolor sit amet eque porro quisquam est, qui dolorem</p>
  <a>READ MORE</a>
</div>

<!-- reviews -->
<section class="reviews">
  <div class="sec-head" style="top:44px">
    <svg width="22" height="22" viewBox="0 0 24 24"><path d="M12 3a9 9 0 018.5 6M21 12a9 9 0 01-15 6.7M3 12a9 9 0 013-6.7" stroke="#333" stroke-width="2.4" fill="none"/></svg>
    <h2>Client Reviews</h2>
  </div>
  <div class="review" style="left:119px">
    <div class="face" role="img" aria-label="Client portrait"></div>
    <div class="quote">&ldquo;</div>
    <h4>Morgan</h4><div class="role">Lorem Ipsum</div>
    <p>Ut enim ad minim veniam, quis nostrud exercitation ullamco laboris nisi ut aliquip ex ea commodo consequat.</p>
    <div class="stars">
      <svg width="82" height="15" viewBox="0 0 82 15"><g fill="#F6B400"><path id="st" d="M7.5 0l2.2 4.6 5 .6-3.7 3.4 1 5-4.5-2.5L3 13.6l1-5L.3 5.2l5-.6z"/><use href="#st" x="16.5"/><use href="#st" x="33"/><use href="#st" x="49.5"/><use href="#st" x="66"/></g></svg>
    </div>
  </div>
  <div class="review" style="left:624px">
    <div class="face" role="img" aria-label="Client portrait"></div>
    <div class="quote">&ldquo;</div>
    <h4>Oliver K.</h4><div class="role">Lorem Ipsum</div>
    <p>Ut enim ad minim veniam, quis nostrud exercitation ullamco laboris nisi ut aliquip ex ea commodo consequat.</p>
    <div class="stars">
      <svg width="82" height="15" viewBox="0 0 82 15"><g fill="#F6B400"><use href="#st"/><use href="#st" x="16.5"/><use href="#st" x="33"/><use href="#st" x="49.5"/><use href="#st" x="66"/></g></svg>
    </div>
  </div>
</section>

<!-- footer -->
<footer class="footer">
  <div class="news-label">Sign up for Newsletter</div>
  <div class="news-form">
    <span><svg width="16" height="12" viewBox="0 0 16 12" fill="none" stroke="#0094D4" stroke-width="1.4"><rect x="1" y="1" width="14" height="10"/><path d="M1 1l7 6 7-6"/></svg>Enter Your Email</span>
    <a class="btn">Get Started</a>
  </div>
  <div class="rule" style="top:169px"></div>

  <div class="fcol" style="left:129px;width:230px">
    <h5>ABOUT US</h5>
    <p style="font-size:13px;line-height:22px;margin-left:-3px">Lorem ipsum dolor sit amet,consectetur adipiscing elit, sed do eiusmod tempor incididunt</p>
    <div class="socials"><i></i><i></i><i></i><i></i></div>
  </div>
  <div class="fcol" style="left:408px;width:300px">
    <h5>CONTACT US</h5>
    <div class="contact-row"><span class="ring"><svg width="10" height="13" viewBox="0 0 10 13"><path d="M5 0a5 5 0 015 5c0 3-5 8-5 8S0 8 0 5a5 5 0 015-5z" fill="#fff"/><circle cx="5" cy="5" r="1.6" fill="#0B1A2B"/></svg></span><span style="font-size:15px;line-height:21px">149 ,Lorem ipsum dolor sit amet<br>United States</span></div>
    <div class="contact-row"><span class="ring"><svg width="12" height="9" viewBox="0 0 12 9" fill="none" stroke="#fff"><rect x=".5" y=".5" width="11" height="8"/><path d="M.5.5l5.5 4 5.5-4"/></svg></span><span style="font-size:15px">info@borrownest.com</span></div>
    <div class="contact-row"><span class="ring"><svg width="12" height="12" viewBox="0 0 24 24"><path fill="#fff" d="M6.6 10.8a15 15 0 006.6 6.6l2.2-2.2c.3-.3.7-.4 1-.2 1.1.4 2.3.6 3.6.6.6 0 1 .4 1 1V20c0 .6-.4 1-1 1A17 17 0 013 4c0-.6.4-1 1-1h3.5c.6 0 1 .4 1 1 0 1.3.2 2.5.6 3.6.1.3 0 .7-.2 1z"/></svg></span><span style="font-size:21px">+1 5552 047 391</span></div>
  </div>
  <div class="fcol" style="left:757px">
    <h5 style="margin-left:5px">QUICK LINKS</h5>
    <ul><li>&raquo; <span>Home</span></li><li>&raquo; <span>About Us</span></li><li>&raquo; <span>Our People</span></li><li>&raquo; <span>Calculators</span></li><li>&raquo; <span>Reviews</span></li></ul>
  </div>
  <div class="fcol" style="left:930px">
    <h5>OTHER LINKS</h5>
    <ul><li>&raquo; <span>Contact Us</span></li><li>&raquo; <span>Loan Options</span></li><li>&raquo; <span>Make Appointment</span></li><li>&raquo; <span>Terms Of Use</span></li><li>&raquo; <span>Privacy Policy</span></li></ul>
  </div>
  <div class="rule" style="top:460px"></div>
  <div class="copy">2022 Borrow Nest. All Rights Reserved</div>
</footer>

</body>
</html>
```